Design and Renovation Company Luxury Business Card

I want to create a luxury business card for a Design and Renovation Firm . We will use our current logo. The company name is 528BUILDA. We do not want anything standard. We need a very unique concept.
Please see uploaded inspiration. I really like the textured paper option. I would like the card to be thick with debossing, and/or embossing options. The logo has orange in it but I would like to see the card with and without the orange. I think the orange may make the company feel less high-end. The goal is to elevate the logo not match its vibe per se of the logo. We want something very unique, not standard at all!
I would like a space for :
Logo,
Name,
Position,
Email,
Office number,
Website Address,
Business Address,
Thank you!
Have fun!
Target Market(s)
Home owners Age 35 +
Industry/Entity Type
Design and Renovation
Contact Information for Business Card
Logo, Name, Position, Email, Office number, Website Address, Business Address,.
Colors
Designer to choose colors to be used in the design.
Requirements
Must have
- A luxury designer feel. Must be black or dark grey but open to other luxury ideas.
Nice to have
- Gold, silver, black embossing or debossing. Textured paper design.
Should not have
- A cheap look and feel.

```html
<!DOCTYPE html>
<html lang="en">
<head>
<meta charset="utf-8">
<title>528BUILDA Business Card</title>
<link href="https://fonts.googleapis.com/css2?family=Poppins:wght@400;500;600&display=swap" rel="stylesheet">
<style>
  :root {
    --page: #e1e6e7;
    --card: #1f1f1f;
    --pattern-dark: #111111;
    --pattern-light: #343434;
    --orange: #f7981f;
    --white: #ffffff;
  }
  * { margin: 0; padding: 0; box-sizing: border-box; }
  html, body {
    width: 1200px; height: 960px; overflow: hidden;
    background: var(--page);
    font-family: "Poppins", sans-serif;
  }
  .card {
    position: absolute; left: 250px; width: 702px; height: 400px;
    background: var(--card); overflow: hidden;
  }
  .card-front { top: 60px; }
  .card-back { top: 500px; }

  .front-pattern {
    position: absolute; inset: 0;
    background: linear-gradient(90deg, var(--pattern-dark) 0%, #1a1a1a 55%, var(--pattern-light) 100%);
  }
  .front-brand {
    position: absolute; right: 68px; top: 330px;
    color: var(--white); font-size: 12px; font-weight: 500; letter-spacing: 1.5px;
    white-space: nowrap;
  }

  .brand-band {
    position: absolute; left: 0; top: 0; width: 114px; height: 400px;
    background: var(--orange);
  }
  .brand-band svg { display: block; }

  .person-name {
    position: absolute; right: 29px; top: 136px; white-space: nowrap; color: var(--white);
    font-size: 38px; font-weight: 400; letter-spacing: 0.5px; line-height: 1;
  }
  .person-name .first { color: var(--orange); font-weight: 600; }
  .person-title {
    position: absolute; right: 29px; top: 176px; white-space: nowrap; color: var(--white);
    font-size: 17px; font-weight: 500; letter-spacing: 0.8px;
  }
  .name-accent {
    position: absolute; left: 683px; top: 146px; width: 19px; height: 55px;
    background: var(--orange);
  }
  .address {
    position: absolute; right: 29px; top: 222px; white-space: nowrap; text-align: right;
    color: var(--orange); font-size: 17.5px; line-height: 26px; letter-spacing: 0.4px;
  }
  .contact-list {
    position: absolute; right: 28px; top: 298px; list-style: none;
  }
  .contact-list li {
    display: flex; justify-content: flex-end; align-items: center; gap: 16px;
    color: var(--white); font-size: 19px; line-height: 25.5px; letter-spacing: 0.3px;
    white-space: nowrap;
  }
  .contact-list svg { width: 17px; height: 17px; flex: none; }
</style>
</head>
<body>

<section class="card card-front" aria-label="Card front">
  <div class="front-pattern" role="img" aria-label="Dark embossed grid of small square tiles across the card, fading lighter toward the right"></div>
  <div class="front-brand">528BUILDA</div>
</section>

<section class="card card-back" aria-label="Card back">
  <div class="brand-band">
    <svg width="114" height="400" viewBox="0 0 114 400">
      <text transform="translate(68 362) rotate(-90)"
            font-family="Poppins, sans-serif" font-size="40" font-weight="600" letter-spacing="2" fill="#ffffff">528BUILDA</text>
      <text transform="translate(88 362) rotate(-90)" textLength="250" lengthAdjust="spacing"
            font-family="Poppins, sans-serif" font-size="11.5" font-weight="500" fill="#ffffff">Design and Renovation Firm</text>
    </svg>
  </div>

  <div class="name-accent"></div>
  <div class="person-name"><span class="first">Marena</span> Voltz</div>
  <div class="person-title">Founder &amp; CEO</div>

  <div class="address">1480 Alder Crest Dr. Suite 300<br>Millbrook, TX 75501</div>

  <ul class="contact-list">
    <li>(555) 014-2287
      <svg viewBox="0 0 24 24" aria-hidden="true"><path fill="#f7981f" d="M6.6 10.8a15.1 15.1 0 0 0 6.6 6.6l2.2-2.2c.3-.3.7-.4 1-.2 1.1.4 2.3.6 3.6.6.6 0 1 .4 1 1V20c0 .6-.4 1-1 1A17 17 0 0 1 3 4c0-.6.4-1 1-1h3.5c.6 0 1 .4 1 1 0 1.3.2 2.5.6 3.6.1.3 0 .7-.2 1z"/></svg>
    </li>
    <li>info@yourwebsite.com
      <svg viewBox="0 0 24 24" aria-hidden="true"><circle cx="12" cy="12" r="9.5" fill="none" stroke="#f7981f" stroke-width="2"/><path d="M2.5 12h19M12 2.5c3 3 3 16 0 19M12 2.5c-3 3-3 16 0 19" fill="none" stroke="#f7981f" stroke-width="1.6"/></svg>
    </li>
    <li>www.yourwebsite.com
      <svg viewBox="0 0 24 24" aria-hidden="true"><rect x="2.5" y="6" width="19" height="14" fill="none" stroke="#f7981f" stroke-width="2"/><path d="M2.5 6l9.5 7 9.5-7" fill="none" stroke="#f7981f" stroke-width="2"/></svg>
    </li>
  </ul>
</section>

</body>
</html>
```